2021 Summer Ads Hollis Bay Custom Homes

We need a re-design of our summer ad run for our customer, Hollis Bay Custom Homes. They are custom home builders in the mostly rural parts of West Virginia, USA. They are known for their "Forever Home" tagline. We'd like two designed ads with the main difference being just the custom home that's featured. These designs should be for a Zintrola banner like 300 x 250 and square ad like 250 x 250. For inspiration please visit the Hollis Bay Custom Homes website at www dot hollisbaycustomhomes dot com

Target Market(s)

consumers / new home shoppers

Industry/Entity Type

Consumer

Requirements
Must have
• HBCH logo
Price Lock Available!
Custom home pic
Learn more >
small CFRM logo mark

```html
<!DOCTYPE html>
<html lang="en">
<head>
<meta charset="utf-8">
<title>Hollis Bay Custom Homes – Summer Ads</title>
<link href="https://fonts.googleapis.com/css2?family=Playfair+Display:wght@700;800&family=Roboto:wght@400;500;700&display=swap" rel="stylesheet">
<style>
  :root {
    --stage: #353535;
    --ad-bg: #111111;
    --red: #c8060c;
    --red-dark: #8f0307;
    --white: #ffffff;
    --badge: #d9d9d9;
    --photo: #7b7f84;
    --label: #ffffff;
  }
  * { margin: 0; padding: 0; box-sizing: border-box; }
  html, body { width: 1200px; height: 771px; overflow: hidden; background: var(--stage); }
  body { position: relative; font-family: "Roboto", Arial, sans-serif; }

  .ad {
    position: absolute;
    width: 300px; height: 250px;
    background: var(--ad-bg);
    overflow: hidden;
    transform-origin: 0 0;
    transform: scale(1.5667);
  }
  .ad--banner { left: 122px; top: 147px; }
  .ad--square { left: 688px; top: 147px; width: 250px; }

  .brand {
    position: absolute;
    display: flex; align-items: center; gap: 3px;
    font-family: "Roboto", Arial, sans-serif;
    font-weight: 700; font-size: 7px; color: var(--red);
    padding: 0 4px; white-space: nowrap;
  }
  .brand--boxed { background: var(--white); }
  .brand__mark { width: 7px; height: 7px; background: var(--red); flex: none; }

  .headline {
    position: absolute;
    font-family: "Playfair Display", Georgia, serif;
    font-weight: 800; color: var(--white);
    letter-spacing: 0.3px; white-space: nowrap; line-height: 1;
  }
  .intro {
    position: absolute;
    color: var(--white); font-weight: 500;
    line-height: 14.5px; text-align: center; white-space: nowrap;
  }
  .price-lock {
    position: absolute;
    color: var(--red); font-weight: 700; text-transform: uppercase;
    line-height: 1.25; text-align: center;
  }
  .cta {
    position: absolute;
    display: flex; align-items: center; justify-content: center; gap: 4px;
    background: var(--red); color: var(--white);
    font-weight: 700; font-size: 6.2px; text-transform: uppercase;
    border-radius: 1px;
  }
  .cta svg { width: 7px; height: 7px; }
  .cfrm-badge { position: absolute; }
  .house-photo { position: absolute; left: 0; }

  .size-label {
    position: absolute; top: 601px;
    width: 200px; margin-left: -100px; text-align: center;
    color: var(--label); font-weight: 700; font-size: 25px;
  }
</style>
</head>
<body>

  <!-- 300 x 250 banner -->
  <section class="ad ad--banner">
    <div class="brand brand--boxed" style="left:3px; top:0; width:67px; height:34px;">
      <span class="brand__mark"></span>Hollis Bay
    </div>
    <h1 class="headline" style="left:85px; top:25px; font-size:17.5px;">FOREVER HOME</h1>
    <p class="intro" style="left:49px; width:250px; top:48px; font-size:8.4px;">They are custom home builders in the mostly rural parts of<br>West Virginia, USA</p>
    <p class="price-lock" style="left:17px; top:79px; font-size:8px;">Price Lock<br>Available !</p>
    <a class="cta" style="left:126px; top:82px; width:68px; height:23px;">Learn more
      <svg viewBox="0 0 10 10"><circle cx="5" cy="5" r="5" fill="#fff"/><path d="M4 3l2 2-2 2" stroke="#c8060c" stroke-width="1.4" fill="none"/></svg>
    </a>
    <svg class="cfrm-badge" style="left:30px; top:106px;" width="26" height="18" viewBox="0 0 26 18"><rect x="0" y="0" width="26" height="18" rx="2" fill="var(--badge)"/></svg>
    <svg class="house-photo" style="top:108px;" width="300" height="142" viewBox="0 0 300 142" role="img" aria-label="Photo of a white custom farmhouse with dark roof, cupola and garage">
      <polygon points="0,50 240,10 300,46 300,142 0,142" fill="var(--photo)"/>
      <polygon points="0,40 238,0 300,36 300,46 240,10 0,50" fill="var(--red)"/>
      <polygon points="0,50 240,10 300,46 300,50 240,14 0,54" fill="var(--red-dark)"/>
    </svg>
  </section>

  <!-- 250 x 250 square -->
  <section class="ad ad--square">
    <svg class="house-photo" style="top:0;" width="250" height="136" viewBox="0 0 250 136" role="img" aria-label="Photo of a white ranch home with a red barn-style garage">
      <polygon points="0,0 250,0 250,128 0,132" fill="var(--photo)"/>
      <polygon points="0,128 250,124 250,130 0,134" fill="var(--red)"/>
    </svg>
    <div class="brand" style="left:88px; top:4px; width:74px; height:26px; justify-content:center;">
      <span class="brand__mark"></span>Hollis Bay
    </div>
    <h1 class="headline" style="left:50px; top:153px; font-size:17.5px;">FOREVER HOME</h1>
    <p class="intro" style="left:0; width:250px; top:176px; font-size:7.9px;">They are custom home builders in the mostly rural parts of<br>West Virginia, USA</p>
    <p class="price-lock" style="left:21px; top:214px; font-size:7px;">Price Lock<br>Available !</p>
    <a class="cta" style="left:91px; top:210px; width:68px; height:23px;">Learn more
      <svg viewBox="0 0 10 10"><circle cx="5" cy="5" r="5" fill="#fff"/><path d="M4 3l2 2-2 2" stroke="#c8060c" stroke-width="1.4" fill="none"/></svg>
    </a>
    <svg class="cfrm-badge" style="left:208px; top:214px;" width="28" height="18" viewBox="0 0 28 18"><rect x="0" y="0" width="28" height="18" rx="2" fill="var(--badge)"/></svg>
  </section>

  <p class="size-label" style="left:357px;">300 * 250</p>
  <p class="size-label" style="left:884px;">250 * 250</p>

</body>
</html>
```